Business Intelligence Application - Reporting Menu and Report Criteria Design

Looking for a fresh, effective and user friendly view for the menu structure and reporting criteria screen format for a business reporting application. Initial format completed, content structure is in place, but we need the 'wow' design.. as its a serious professional report/BI tool it has to fall within certain guidelines for clarity and graphics..but we want it to be slick, friendly, great user experience. There is a large amount of complex content to fit into a small space and we need it to be very inviting, modern and intuitive.. If interested, please review the attachment. We have live screens in operation, but feel these could be improved and looking forward to seeing what great creative suggestions could be made. Please review work done to date in the attached.. We are not looking for a total re-design of everything, all the basic business content/structure is there.. but tell us what we could do to improve this in terms of graphic design... particularly the criteria screens.. thanks!
Updates

Reason: Need a few more days to review designs - thanks for all submissions so far, we will make a selection shortly.

Target Market(s)

Business analysts, hotel operations teams, finance analysts hospitality industry

Industry/Entity Type

Hospitality

Coding

Coded - Design and coding required

Number of Pages Required

4 page

Font styles to use
Sans Serif
Other font styles liked:
• Candara, please see example in deck

Colors
3276b5
3176b5
0255a3
85acd3
33a6d7
cee9f5
85cae6

Requirements
Must have
• sharp clear, logical menu structure, (currently it has 'clicks to sub-menus, we need hover over, slide to sub-menus..) colour, styling.. and most focus on revision of criteria.. right now is somewhat heavy, cumbersome.. keep colour and friendly intuitive process steps.. its heavy analytical stuff.. best of luck!
Should not have
• No grey fonts on white or grey screens! many business apps are not readable or sharp.. or fonts are too small.. colourless, so please avoid that.. see our deck - sharp dark (navy) or black fonts on white, or light shading..

```html
<!DOCTYPE html>
<html lang="en">
<head>
<meta charset="utf-8">
<title>HX Insight – Property Search</title>
<link href="https://fonts.googleapis.com/css2?family=Mulish:wght@400;600;700&display=swap" rel="stylesheet">
<style>
:root{
  --navy:#00183a;
  --nav-blue:#0255a3;
  --nav-active:#4ab0dc;
  --body-top:#33a6d7;
  --body-bottom:#0b5fae;
  --panel-top:#55b7df;
  --panel-bottom:#3298d0;
  --field-top:#ffffff;
  --field-bottom:#ececec;
  --field-border:#c9d3da;
  --field-text:#555b61;
  --white:#ffffff;
  --bell:#1f86c9;
  --divider:#1b3356;
  --footer-bg:#e0e0e0;
  --footer-text:#6f6f6f;
  --button:#0255a3;
}
*{box-sizing:border-box;margin:0;padding:0}
html,body{width:1200px;height:664px;overflow:hidden}
body{font-family:"Mulish",sans-serif;position:relative;background:var(--body-bottom)}
.app-header{position:absolute;left:0;top:0;width:1200px;height:113px;background:var(--navy)}
.brand{position:absolute;left:97px;top:40px;display:flex;align-items:center;gap:14px}
.brand-mark{width:30px;height:30px;background:var(--nav-active)}
.brand-name{font-size:27px;font-weight:700;color:var(--white);letter-spacing:.2px}
.user-box{position:absolute;left:781px;top:35px;display:flex;align-items:center;gap:9px}
.avatar{width:44px;height:44px;border-radius:50%;background:radial-gradient(circle at 50% 40%,#c9b8a6,#6e7a82)}
.user-text{color:var(--white);font-size:14px;line-height:21px}
.user-text strong{font-weight:600}
.header-divider{position:absolute;top:39px;width:1px;height:40px;background:var(--divider)}
.header-icon{position:absolute}
.main-nav{position:absolute;left:0;top:113px;width:1200px;height:51px;background:var(--nav-blue);display:flex;padding-left:97px}
.nav-item{display:flex;align-items:center;justify-content:center;gap:8px;color:var(--white);font-size:18px;font-weight:700;height:51px;border-right:1px solid rgba(255,255,255,.55)}
.nav-item:last-child{border-right:none}
.nav-item.is-active{background:var(--nav-active);border-right:none}
.nav-item svg{fill:var(--white)}
.workspace{position:absolute;left:0;top:164px;width:1200px;height:425px;background:linear-gradient(var(--body-top),var(--body-bottom))}
.search-panel{position:absolute;left:112px;top:19px;width:974px;height:320px;background:linear-gradient(var(--panel-top),var(--panel-bottom))}
.field{position:absolute;width:282px}
.field-label{display:block;color:var(--white);font-size:17px;font-weight:700;height:22px;line-height:22px}
.field-label.is-plain{font-weight:600}
.field-input{display:block;margin-top:10px;width:282px;height:43px;border:1px solid var(--field-border);background:linear-gradient(var(--field-top),var(--field-bottom));font:400 16px "Mulish",sans-serif;color:var(--field-text);padding:0 17px;line-height:41px}
.search-button{position:absolute;left:708px;top:233px;width:215px;height:51px;background:var(--button);color:var(--white);font:700 20px "Mulish",sans-serif;border:none;text-align:center;line-height:51px}
.app-footer{position:absolute;left:0;top:589px;width:1200px;height:75px;background:var(--footer-bg);text-align:center;color:var(--footer-text);font-size:13px;line-height:44px}
</style>
</head>
<body>
<header class="app-header">
  <div class="brand"><span class="brand-mark"></span><span class="brand-name">HX Insight</span></div>
  <div class="user-box">
    <div class="avatar" role="img" aria-label="Profile photo of the signed-in administrator"></div>
    <div class="user-text">Welcome<br><strong>Admin</strong></div>
  </div>
  <span class="header-divider" style="left:919px"></span>
  <svg class="header-icon" style="left:946px;top:42px" width="28" height="30" viewBox="0 0 28 30" aria-label="Notifications"><path fill="var(--bell)" d="M14 2c-1.3 0-2 .9-2 2v1C7.8 6 5.5 9.5 5.5 14v6L2 24h24l-3.5-4v-6c0-4.5-2.3-8-6.5-9V4c0-1.1-.7-2-2-2zM10.5 26a3.5 3.5 0 0 0 7 0z"/></svg>
  <span class="header-divider" style="left:1005px"></span>
  <svg class="header-icon" style="left:1036px;top:45px" width="28" height="22" viewBox="0 0 28 22" aria-label="Sign out"><path fill="var(--bell)" d="M17 1l10 8.5L17 18v-5C9 13 4 15 1 21c1-8 6-14 16-15z"/></svg>
</header>

<nav class="main-nav">
  <div class="nav-item" style="width:115px">
    <svg width="22" height="22" viewBox="0 0 22 22"><circle cx="11" cy="6" r="5"/><path d="M1 21c0-5 4-8 10-8s10 3 10 8z"/></svg>Admin
  </div>
  <div class="nav-item" style="width:194px">
    <svg width="28" height="24" viewBox="0 0 28 24"><rect x="10" y="0" width="8" height="7" rx="1"/><rect x="0" y="16" width="8" height="7" rx="1"/><rect x="10" y="16" width="8" height="7" rx="1"/><rect x="20" y="16" width="8" height="7" rx="1"/><path d="M13 7h2v4h9v5h-2v-3h-7v3h-2v-3H6v3H4v-5h9z"/></svg>Management
  </div>
  <div class="nav-item is-active" style="width:228px">
    <svg width="20" height="20" viewBox="0 0 20 20"><path d="M8 0a8 8 0 1 0 4.9 14.3l5 5 2.1-2.1-5-5A8 8 0 0 0 8 0zm0 3a5 5 0 1 1 0 10A5 5 0 0 1 8 3z"/></svg>Property Search
  </div>
  <div class="nav-item" style="width:133px">
    <svg width="22" height="22" viewBox="0 0 22 22"><circle cx="11" cy="11" r="11"/><path fill="var(--nav-blue)" d="M6 4c2 1 3 3 2 5s-3 2-3 4 2 3 2 5c-3-1-5-4-5-7 0-3 2-6 4-7zm9 1c2 0 3 2 3 4s-2 2-3 1-2 0-2-2 1-3 2-3zm-1 9c2 0 3 1 2 3s-3 2-3 0 0-3 1-3z"/></svg>Intel
  </div>
  <div class="nav-item" style="width:145px">
    <svg width="24" height="24" viewBox="0 0 24 24"><circle cx="12" cy="12" r="8"/><circle cx="12" cy="12" r="10" fill="none" stroke="#fff" stroke-width="4" stroke-dasharray="4 3.85"/><circle cx="12" cy="12" r="3.5" fill="var(--nav-blue)"/></svg>Planning
  </div>
</nav>

<main class="workspace">
  <form class="search-panel">
    <div class="field" style="left:45px;top:42px"><label class="field-label">SEARCH NAME</label><div class="field-input">Royal..</div></div>
    <div class="field" style="left:344px;top:42px"><label class="field-label">SEARCH ID</label><div class="field-input"></div></div>
    <div class="field" style="left:639px;top:42px"><label class="field-label">SEARCH PRODUCT</label><div class="field-input"></div></div>
    <div class="field" style="left:45px;top:143px"><label class="field-label">DIVISIONS</label><div class="field-input">North Amercia</div></div>
    <div class="field" style="left:344px;top:143px"><label class="field-label">REGIONS</label><div class="field-input"></div></div>
    <div class="field" style="left:639px;top:143px"><label class="field-label is-plain">Areas</label><div class="field-input"></div></div>
    <div class="search-button">SEARCH</div>
  </form>
</main>

<footer class="app-footer">© 2017 Company Name&nbsp; All right reserved&nbsp; Term of Use</footer>
</body>
</html>
```